Tally Roster survey and prize

We need an A4 poster design for a survey and competition I wish to hold. The survey will be on Poll Heron. My website www.TallyRoster.com.au will redirect the users to the survey page. I will be selecting a survey entrant at random to win a prize. The prize is $200 cash. The survey will be open for two months as the mail out of this poster will go throughout Victoria, Australia. The competition end date is yet to be decided - depends on when I can get this poster completed and the mail out done.

The mail out is targeting the Aged Care industry workers and decision makers. It hopefully will be placed on a notice board in the facilities and need to attract attention for people to visit my site and then take the survey.

The survey is for not for residents but for the workers in the facility.

Reason: Just got some feedback on required content of the poster. Text for the poster required: "The survey is for determining a market for rostering and payroll software, your assitance in taking this survey would be greatly appreciated." Martin Holloway

Target Market(s)

Workers in Aged Care industry and decision makers.

Industry/Entity Type

Industry

Requirements
Must have
• 1. Must reference the website www.TallyRoster.com.au.
2. Must mention that there is a prize of $200.
3. Must mention that entry to the competition is dependant on taking the survey.
4. Must mention the close date (date yet to be decided).
5. Must mention winning contestant will be contacted by phone.

```html
<!DOCTYPE html>
<html lang="en">
<head>
<meta charset="utf-8">
<title>Tally Roster Survey Poster</title>
<link rel="stylesheet" href="https://fonts.googleapis.com/css2?family=Bebas+Neue&family=Roboto:wght@400;700;900&display=swap">
<style>
  :root {
    --cream: #fdf6e6;
    --brand-blue: #3f66a0;
    --ink: #2b2d33;
    --panel: #363843;
    --sun: #fcd95a;
    --white: #ffffff;
    --shade: #1d2a40;
    --garden-top: #6f7f4a;
    --garden-bottom: #9c8466;
  }
  html, body {
    margin: 0;
    padding: 0;
    overflow: hidden;
    background: var(--cream);
  }
  .poster {
    position: relative;
    width: 848px;
    height: 1200px;
    background: var(--cream);
    overflow: hidden;
    font-family: "Roboto", Arial, sans-serif;
    color: var(--ink);
  }
  .top-band {
    position: absolute;
    left: 0; top: 0;
    width: 848px; height: 34px;
    background: var(--brand-blue);
  }
  .hero-photo {
    position: absolute;
    left: 21px; top: 90px;
    width: 584px; height: 601px;
    background: linear-gradient(180deg, var(--garden-top) 0%, var(--garden-bottom) 100%);
  }
  .headline {
    position: absolute;
    left: 608px; top: 90px;
    width: 228px; height: 604px;
  }
  .headline text {
    font-family: "Bebas Neue", "Oswald", sans-serif;
  }
  .headline .dark { fill: var(--ink); }
  .headline .blue { fill: var(--brand-blue); }
  .headline .rule { stroke: var(--brand-blue); stroke-width: 2; }
  .prize-badge {
    position: absolute;
    left: 48px; top: 636px;
    width: 370px; height: 380px;
  }
  .prize-badge text {
    font-family: "Roboto", "Arial Black", sans-serif;
    font-weight: 900;
  }
  .survey-panel {
    position: absolute;
    left: 459px; top: 738px;
    width: 348px; height: 264px;
    background: var(--panel);
    border-radius: 32px;
    box-shadow: 4px 6px 8px rgba(0,0,0,0.35);
    color: var(--white);
    text-align: center;
  }
  .survey-panel .invite {
    margin: 56px 0 0;
    font-size: 30px;
    line-height: 36px;
    font-weight: 400;
  }
  .survey-panel .site {
    margin: 46px 0 0;
    font-size: 21px;
    line-height: 30px;
  }
  .survey-panel .site-name {
    font-size: 29px;
    font-weight: 700;
    color: var(--sun);
  }
  .closing {
    position: absolute;
    left: 0; top: 1070px;
    width: 848px;
    text-align: center;
  }
  .closing .date-line {
    margin: 0;
    font-size: 31px;
    line-height: 38px;
    color: #111;
  }
  .closing .date-line strong { font-weight: 700; }
  .closing .notice {
    margin: 4px 0 0;
    font-size: 18px;
    color: #222;
  }
  .bottom-band {
    position: absolute;
    left: 0; top: 1166px;
    width: 848px; height: 34px;
    background: var(--brand-blue);
    color: var(--white);
    font-size: 17px;
    line-height: 34px;
    text-align: center;
  }
</style>
</head>
<body>
<div class="poster">
  <div class="top-band"></div>

  <div class="hero-photo" role="img" aria-label="Photo of an elderly couple in a garden"></div>

  <svg class="headline" viewBox="0 0 228 604" aria-label="Take the survey, enter the competition, become the winner">
    <text class="dark" x="2" y="90" font-size="120" textLength="224" lengthAdjust="spacingAndGlyphs">TAKE THE</text>
    <text class="blue" x="2" y="214" font-size="160" textLength="224" lengthAdjust="spacingAndGlyphs">SURVEY</text>
    <text class="dark" x="2" y="298" font-size="112" textLength="224" lengthAdjust="spacingAndGlyphs">ENTER THE</text>
    <text class="blue" x="2" y="370" font-size="90" textLength="224" lengthAdjust="spacingAndGlyphs">COMPETETION</text>
    <text class="dark" x="2" y="470" font-size="140" textLength="224" lengthAdjust="spacingAndGlyphs">BECOME</text>
    <line class="rule" x1="2" y1="506" x2="226" y2="506"/>
    <text class="blue" x="2" y="584" font-size="100" textLength="224" lengthAdjust="spacingAndGlyphs">THE WINNER</text>
    <line class="rule" x1="2" y1="600" x2="226" y2="600"/>
  </svg>

  <svg class="prize-badge" viewBox="0 0 370 380" aria-label="Win $200 cash">
    <defs>
      <clipPath id="badge-disc">
        <circle cx="184" cy="188" r="182"/>
      </clipPath>
    </defs>
    <circle cx="184" cy="188" r="182" fill="var(--brand-blue)"/>
    <polygon clip-path="url(#badge-disc)" points="0,341 370,246 370,380 0,380" fill="var(--sun)"/>
    <g transform="rotate(-15 184 170)">
      <text x="170" y="140" text-anchor="middle" font-size="100" fill="var(--shade)" opacity="0.5" dx="4" dy="4" textLength="184" lengthAdjust="spacingAndGlyphs">WIN</text>
      <text x="170" y="140" text-anchor="middle" font-size="100" fill="var(--white)" textLength="184" lengthAdjust="spacingAndGlyphs">WIN</text>
      <text x="192" y="256" text-anchor="middle" font-size="110" fill="var(--shade)" opacity="0.5" dx="4" dy="4" textLength="222" lengthAdjust="spacingAndGlyphs">$200</text>
      <text x="192" y="256" text-anchor="middle" font-size="110" fill="var(--white)" textLength="222" lengthAdjust="spacingAndGlyphs">$200</text>
    </g>
    <text x="230" y="318" text-anchor="middle" font-size="44" fill="var(--ink)" transform="rotate(-15 230 304)">CASH</text>
  </svg>

  <div class="survey-panel">
    <p class="invite">Complete our<br>online survey at</p>
    <p class="site">www.<span class="site-name">TallyRoster</span>.com.au</p>
  </div>

  <div class="closing">
    <p class="date-line"><strong>Closing Date</strong> xx-xx-xxxx</p>
    <p class="notice">Winning Contestant will be Informed by Phone</p>
  </div>

  <div class="bottom-band">Winning Contestant will be Informed by Phone</div>
</div>
</body>
</html>
```